Moravel Aesthetic Doctor

I require an elegant, luxurious looking business card for my aesthetic business. I am a doctor and that will set me aside from competitors. I am planning to provide home and spa based treatments to clients with high expectations. I have attached my logo.

```html
<!DOCTYPE html>
<html lang="en">
<head>
<meta charset="utf-8">
<title>Moravel Aesthetic Doctor – Business Card</title>
<link rel="stylesheet" href="https://fonts.googleapis.com/css2?family=Cormorant+Garamond:wght@500;700&family=Quicksand:wght@400;500&display=swap">
<style>
  :root {
    --bg: #e9eaec;
    --card: #ffffff;
    --blue: #1aa6e6;
    --blue-deep: #1b8fd0;
    --grey: #a7a9ac;
    --grey-text: #8a8c8f;
    --white: #ffffff;
  }
  * { margin: 0; padding: 0; box-sizing: border-box; }
  html, body { width: 1200px; height: 965px; overflow: hidden; background: var(--bg); }
  .stage { position: relative; width: 1200px; height: 965px; }

  .card {
    position: absolute; left: 220px; width: 760px; height: 434px;
    background: var(--card); overflow: hidden;
    box-shadow: 0 6px 18px rgba(0,0,0,0.12);
  }
  .card--front { top: 34px; }
  .card--back { top: 498px; }

  /* business name set as plain text */
  .brand-name {
    position: absolute; white-space: nowrap;
    font-family: "Quicksand", sans-serif; font-weight: 500;
    color: var(--grey-text); line-height: 1;
  }
  .card--front .brand-name { left: 0; right: 0; top: 150px; text-align: center; font-size: 40px; }
  .card--back .brand-name { left: 40px; top: 60px; font-size: 30px; }

  .rule { position: absolute; height: 2px; background: var(--grey); }
  .rule--right { left: 480px; top: 220px; width: 230px; }
  .rule--left { left: 50px; top: 372px; width: 230px; }

  .services {
    position: absolute; left: 0; right: 0; top: 250px; text-align: center;
    font-family: "Quicksand", sans-serif; font-weight: 500; font-size: 21px;
    line-height: 1.35; color: var(--blue);
  }

  /* back */
  .shapes { position: absolute; inset: 0; }
  .doctor {
    position: absolute; right: 40px; top: 205px; text-align: right;
    font-family: "Quicksand", sans-serif; color: var(--grey-text);
  }
  .doctor__line { white-space: nowrap; }
  .doctor__name {
    font-family: "Cormorant Garamond", serif; font-weight: 700;
    font-size: 40px; color: var(--blue-deep);
  }
  .doctor__post { font-size: 20px; padding-left: 10px; margin-left: 8px; border-left: 2px solid var(--grey-text); }
  .doctor__diploma { font-size: 20px; margin-top: 2px; }

  .band-label {
    position: absolute; right: 30px; top: 393px; white-space: nowrap;
    font-family: "Cormorant Garamond", serif; font-weight: 500; font-size: 18px;
    letter-spacing: 1px; color: var(--white);
  }

  .social { position: absolute; left: 50px; top: 258px; display: flex; gap: 12px; }
  .social__dot { width: 26px; height: 26px; border-radius: 50%; background: var(--blue); }

  .contact {
    position: absolute; left: 50px; top: 320px; list-style: none;
    font-family: "Quicksand", sans-serif; font-size: 21px; color: var(--white);
  }
  .contact__item { display: flex; align-items: center; gap: 12px; height: 33px; }
  .contact__icon { width: 20px; height: 20px; flex: none; }
</style>
</head>
<body>
<main class="stage">

  <section class="card card--front" aria-label="Card front">
    <div class="brand-name">Moravel Aesthetic Doctor</div>
    <div class="rule rule--right"></div>
    <p class="services">
      Dermal injectables - Plasma facials - Microneedling<br>
      Skin boosters - Excessive sweating<br>
      Home and Spa Based Treatments
    </p>
    <div class="rule rule--left"></div>
  </section>

  <section class="card card--back" aria-label="Card back">
    <svg class="shapes" width="760" height="434" viewBox="0 0 760 434">
      <polygon points="360,376 760,376 760,434 400,434" fill="var(--blue)"/>
      <polygon points="0,298 260,298 390,434 0,434" fill="var(--grey)"/>
    </svg>

    <div class="brand-name">Moravel Aesthetic Doctor</div>

    <div class="doctor">
      <div class="doctor__line"><span class="doctor__name">Dr Elena Varsk</span><span class="doctor__post">MRCPCH MD</span></div>
      <div class="doctor__diploma">Australasian Diploma of Aesthetic Medicine</div>
    </div>

    <div class="band-label">HOME AND SPA BASED TREATMENTS</div>

    <div class="social" aria-label="Social media">
      <span class="social__dot"></span>
      <span class="social__dot"></span>
    </div>

    <ul class="contact">
      <li class="contact__item">
        <svg class="contact__icon" viewBox="0 0 20 20" fill="none" stroke="#fff" stroke-width="1.6" stroke-linejoin="round"><path d="M4 2 L8 2 L9 6 L7 8 Q9 12 12 13 L14 11 L18 12 L18 16 Q16 18 13 17 Q5 14 3 6 Q2 3 4 2 Z"/></svg>
        <span>0800 555 014</span>
      </li>
      <li class="contact__item">
        <svg class="contact__icon" viewBox="0 0 20 20" fill="none" stroke="#fff" stroke-width="1.6"><rect x="2" y="4" width="16" height="12"/><path d="M2 4 L10 11 L18 4"/></svg>
        <span>elena@moravel.co.nz</span>
      </li>
      <li class="contact__item">
        <svg class="contact__icon" viewBox="0 0 20 20" fill="none" stroke="#fff" stroke-width="1.6"><circle cx="10" cy="10" r="8"/><ellipse cx="10" cy="10" rx="3.5" ry="8"/><path d="M2 10 H18"/></svg>
        <span>www.moravel.co.nz</span>
      </li>
    </ul>
  </section>

</main>
</body>
</html>
```